Personal training and nutrition business needs business card design

We need a business card that outlays our services and invites potential customers to join our team and take the first step to a healthier and more enjoyable life. We cater for any level of fitness and specialize in weight loss and conditioning, strength training, muscle gain and strength endurance. Whether you are just starting off or need some help getting to the next level of your journey we are here to get the job done.
We specialize in one on one or one on two personal training sessions and each program will be custom made to suit individual fitness goals of our clients

```html
<!DOCTYPE html>
<html lang="en">
<head>
<meta charset="utf-8">
<title>Stride &amp; Form — Business Card</title>
<link rel="stylesheet" href="https://fonts.googleapis.com/css2?family=Exo+2:ital,wght@1,800&family=Oswald:wght@500&family=Roboto:wght@400;900&display=swap">
<style>
  :root {
    --backdrop: #2b2b2c;
    --card: #1c1c1d;
    --emboss: #4a4a4c;
    --purple: #9550c0;
    --purple-soft: #a865cf;
    --text: #ececec;
  }
  * { margin: 0; padding: 0; box-sizing: border-box; }
  html, body { width: 1200px; height: 1138px; overflow: hidden; }
  body { background: var(--backdrop); position: relative; font-family: "Roboto", sans-serif; }

  .card {
    position: absolute;
    width: 620px;
    height: 374px;
    background: var(--card);
    border-radius: 14px;
    box-shadow: 0 6px 16px rgba(0,0,0,0.45);
  }
  .card--front { left: 274px; top: 186px; }
  .card--back  { left: 276px; top: 608px; }

  /* Front */
  .front-brand {
    position: absolute;
    left: 0; right: 0; top: 150px;
    display: flex; align-items: center; justify-content: center; gap: 16px;
  }
  .front-brand__mark { width: 46px; height: 46px; background: var(--emboss); }
  .front-brand__name {
    font-family: "Roboto", sans-serif; font-weight: 900;
    font-size: 48px; letter-spacing: 2px; color: var(--emboss);
  }
  .tagline {
    font-family: "Oswald", sans-serif; font-weight: 500;
    color: var(--purple); text-transform: uppercase; letter-spacing: 1.2px;
  }
  .card--front .tagline {
    position: absolute; left: 0; right: 0; top: 333px;
    text-align: center; font-size: 13px;
  }

  /* Back, left column */
  .back-brand { position: absolute; left: 82px; top: 96px; width: 196px; text-align: center; }
  .back-brand__mark { width: 54px; height: 54px; background: var(--purple); margin: 0 auto 18px; }
  .back-brand__name {
    font-family: "Roboto", sans-serif; font-weight: 900;
    font-size: 32px; line-height: 32px; color: var(--text); letter-spacing: 1px;
  }
  .card--back .tagline { font-size: 8.5px; margin-top: 8px; letter-spacing: 0.6px; }

  /* Back, right column */
  .contact { position: absolute; left: 342px; top: 84px; }
  .contact__name {
    font-family: "Exo 2", sans-serif; font-weight: 800; font-style: italic;
    font-size: 25px; color: var(--purple-soft); letter-spacing: 0.5px; line-height: 28px;
  }
  .contact__role { font-size: 16px; color: var(--text); margin-top: 4px; }
  .contact__list { list-style: none; margin-top: 27px; }
  .contact__item {
    display: flex; align-items: center; gap: 16px;
    font-size: 16px; color: var(--text); height: 24.5px;
  }
  .contact__item svg { width: 14px; height: 14px; flex: none; }
  .contact__address { font-size: 16px; line-height: 24px; color: var(--text); margin-top: 6px; }
</style>
</head>
<body>

<section class="card card--front">
  <div class="front-brand">
    <span class="front-brand__mark"></span>
    <span class="front-brand__name">STRIDE &amp; FORM</span>
  </div>
  <p class="tagline">Personal training.&nbsp; Nutrition. Motivation</p>
</section>

<section class="card card--back">
  <div class="back-brand">
    <div class="back-brand__mark"></div>
    <div class="back-brand__name">STRIDE<br>&amp; FORM</div>
    <p class="tagline">Personal training.&nbsp; Nutrition. Motivation</p>
  </div>

  <div class="contact">
    <h1 class="contact__name">MARK RIVERS</h1>
    <p class="contact__role">Personal Trainer</p>
    <ul class="contact__list">
      <li class="contact__item">
        <svg viewBox="0 0 14 14" aria-hidden="true"><path fill="var(--purple)" d="M2 5c0-2 2-3 5-3s5 1 5 3l-2 1-1-2H5L4 6zM3 7h8l1 5H2z"/><circle cx="7" cy="9.5" r="1.3" fill="#1c1c1d"/></svg>
        +1 (555) 014-2280
      </li>
      <li class="contact__item">
        <svg viewBox="0 0 14 14" aria-hidden="true"><rect x="1" y="3" width="12" height="9" fill="var(--purple)"/><path d="M1 3l6 5 6-5" stroke="#1c1c1d" stroke-width="1.2" fill="none"/></svg>
        mark@strideform.com
      </li>
      <li class="contact__item">
        <svg viewBox="0 0 14 14" aria-hidden="true"><circle cx="7" cy="7" r="6" fill="var(--purple)"/><path d="M1 7h12M7 1v12M7 1c-3 3-3 9 0 12M7 1c3 3 3 9 0 12" stroke="#1c1c1d" stroke-width="0.9" fill="none"/></svg>
        www.strideform.com
      </li>
    </ul>
    <p class="contact__address">1420 Cedar Ridge Lane<br>Fairview Texas 75000</p>
  </div>
</section>

</body>
</html>
```